Tolvik Commercial Cleaning is lookong for a new business card design.

A fresh new design that's professional and stylish. We need a serious upgrade to our business cards. I have included pictures of our existing ones. Our clients include professional individuals and business owners. We woupdblike something professional and upbeat. Please have fun and see what you come uo with.

Target Market(s)

Property managers, business owners, facility managers and other similar professionals

Industry/Entity Type

Janitorial

Contact Information for Business Card

Name, cell, office number, email, web address

Font styles to use
Sans Serif

Colors

Designer to choose colors to be used in the design.

Requirements
Must have
• please use the green color in our logo
Nice to have
• Bar code
Should not have
• Address

```html
<!DOCTYPE html>
<html lang="en">
<head>
<meta charset="utf-8">
<title>Tolvik Commercial Cleaning – Business Card</title>
<link rel="stylesheet" href="https://fonts.googleapis.com/css2?family=Montserrat:wght@600;700&family=Open+Sans:wght@400&display=swap">
<style>
  :root {
    --backdrop: #232325;
    --card-dark: #202024;
    --brand-green: #3ab75a;
    --brand-green-deep: #2f9a48;
    --brand-blue: #3f72b3;
    --ink-light: #f2f2f2;
    --deco-dark: #2b2b30;
  }
  * { box-sizing: border-box; margin: 0; padding: 0; }
  html, body { width: 1200px; height: 780px; overflow: hidden; }
  body {
    background: var(--backdrop);
    position: relative;
    font-family: "Open Sans", sans-serif;
  }
  .card {
    position: absolute;
    top: 235px;
    width: 540px;
    height: 310px;
    border-radius: 18px;
    background: var(--card-dark);
    overflow: hidden;
    box-shadow: 0 12px 30px rgba(0,0,0,.45);
  }
  .card--front { left: 30px; }
  .card--back { left: 630px; }

  /* front */
  .front-band {
    position: absolute;
    left: 0; right: 0;
    top: 44px; height: 222px;
    background: var(--brand-green);
    display: flex;
    flex-direction: column;
    align-items: center;
    justify-content: center;
  }
  .front-name {
    font-family: "Montserrat", sans-serif;
    font-weight: 700;
    font-size: 84px;
    line-height: 1;
    letter-spacing: -1px;
    color: var(--brand-green-deep);
  }
  .front-tagline {
    margin-top: 10px;
    font-family: "Montserrat", sans-serif;
    font-weight: 700;
    font-size: 19px;
    letter-spacing: 1px;
    color: var(--brand-green-deep);
  }

  /* back */
  .back-decor {
    position: absolute;
    left: -118px;
    top: 118px;
    transform: rotate(90deg);
    font-family: "Montserrat", sans-serif;
    font-weight: 700;
    font-size: 96px;
    line-height: 1;
    color: var(--deco-dark);
    white-space: nowrap;
  }
  .back-brand {
    position: absolute;
    right: 34px;
    top: 30px;
    text-align: right;
  }
  .back-brand__name {
    font-family: "Montserrat", sans-serif;
    font-weight: 700;
    font-size: 62px;
    line-height: 1;
    letter-spacing: -1px;
    color: var(--brand-green);
  }
  .back-brand__tagline {
    margin-top: 6px;
    font-family: "Montserrat", sans-serif;
    font-weight: 700;
    font-size: 14px;
    letter-spacing: .5px;
    color: var(--brand-blue);
  }
  .holder {
    position: absolute;
    right: 20px;
    top: 150px;
    display: flex;
    align-items: center;
    gap: 8px;
    font-family: "Montserrat", sans-serif;
    font-weight: 700;
    font-size: 27px;
  }
  .holder__first { color: var(--brand-green); }
  .holder__last { color: var(--brand-blue); }
  .holder__marker {
    width: 12px; height: 26px;
    background: var(--brand-green);
  }
  .contacts {
    position: absolute;
    right: 20px;
    top: 206px;
    list-style: none;
    text-align: right;
  }
  .contacts li {
    display: flex;
    justify-content: flex-end;
    align-items: center;
    gap: 8px;
    font-size: 14px;
    line-height: 24px;
    color: var(--ink-light);
  }
  .contacts svg { width: 14px; height: 14px; flex: none; }
</style>
</head>
<body>
  <section class="card card--front" aria-label="Card front">
    <div class="front-band">
      <div class="front-name">Tolvik</div>
      <div class="front-tagline">commercial cleaning</div>
    </div>
  </section>

  <section class="card card--back" aria-label="Card back">
    <div class="back-decor" aria-hidden="true">Tolvik</div>

    <div class="back-brand">
      <div class="back-brand__name">Tolvik</div>
      <div class="back-brand__tagline">commercial cleaning</div>
    </div>

    <div class="holder">
      <span class="holder__first">Dara</span>
      <span class="holder__last">Menfield</span>
      <span class="holder__marker"></span>
    </div>

    <ul class="contacts">
      <li>(555) 014-2290
        <svg viewBox="0 0 16 16" aria-hidden="true"><path fill="#3ab75a" d="M3.5 1.5l2.3 0 1.1 3-1.5 1.2a8 8 0 0 0 4.9 4.9l1.2-1.5 3 1.1 0 2.3c0 .8-.7 1.5-1.5 1.5A12.5 12.5 0 0 1 2 3c0-.8.7-1.5 1.5-1.5z"/></svg>
      </li>
      <li>dara@tolvikclean.com
        <svg viewBox="0 0 16 16" aria-hidden="true"><rect x="1" y="3" width="14" height="10" rx="1.5" fill="#3ab75a"/><path d="M1.5 4l6.5 5 6.5-5" fill="none" stroke="#202024" stroke-width="1.4"/></svg>
      </li>
      <li>www.tolvikclean.com
        <svg viewBox="0 0 16 16" aria-hidden="true"><circle cx="8" cy="8" r="6.5" fill="none" stroke="#3ab75a" stroke-width="1.5"/><ellipse cx="8" cy="8" rx="2.8" ry="6.5" fill="none" stroke="#3ab75a" stroke-width="1.2"/><path d="M1.5 8h13" stroke="#3ab75a" stroke-width="1.2"/></svg>
      </li>
    </ul>
  </section>
</body>
</html>
```